Verodex business card

Business card for sustainable investment company called "Verodex". Verodex is an exchange platform selling carbon credits between buyers and sellers. Carbon Credits are an environmental commodity for reducing global carbon emissions.

the card should obviously have our logo and the theme should be sustainability/environment mixed with a trading platform.

Contact Information for Business Card

Logo, Name, Title, Phone, Email

Colors
0054AA
0677BA
7BADD7
CADEEF
E8F1F8
0094D4
00A9DD
6FCCEA
C7EBF8
E9F6FB
00AB8E
00BBA5
67D7C9
C6EFE9
E9F9F6
59FF00
82FF00
B8FF75
E3FFCB
F4FFEA

```html
<!DOCTYPE html>
<html lang="en">
<head>
<meta charset="utf-8">
<title>Verodex business card</title>
<link href="https://fonts.googleapis.com/css2?family=Poppins:wght@400;600&display=swap" rel="stylesheet">
<style>
  :root {
    --backdrop: #1c2624;
    --card: #0f1e1c;
    --card-edge: #132825;
    --teal: #00bba5;
    --teal-deep: #00ab8e;
    --mint: #67d7c9;
    --lime: #82ff00;
    --leaf: #59ff00;
    --ocean: #0094d4;
    --marine: #0677ba;
    --pale: #e9f9f6;
    --soft: #c6efe9;
  }
  * { box-sizing: border-box; margin: 0; padding: 0; }
  html, body {
    width: 1200px; height: 842px; overflow: hidden;
    background: var(--backdrop);
    font-family: "Poppins", sans-serif;
  }
  .canvas {
    position: relative; width: 1200px; height: 842px;
    display: flex; align-items: center; justify-content: center; gap: 40px;
  }
  .card {
    position: relative; width: 540px; height: 309px;
    background: linear-gradient(160deg, var(--card-edge), var(--card));
    overflow: hidden;
    box-shadow: 0 10px 30px rgba(0,0,0,.45);
  }

  /* Back side: contact details */
  .card-back .band-top {
    position: absolute; left: 0; top: 0; width: 100%; height: 14px;
    background: linear-gradient(90deg, var(--teal-deep), var(--teal), var(--lime));
  }
  .card-back .band-bottom {
    position: absolute; left: 0; bottom: 0; width: 100%; height: 14px;
    background: linear-gradient(90deg, var(--marine), var(--ocean), var(--teal));
  }
  .contact {
    position: absolute; inset: 0;
    display: flex; flex-direction: column; align-items: center; justify-content: center;
    text-align: center; text-transform: uppercase;
  }
  .contact .name {
    color: var(--teal); font-weight: 600; font-size: 22px; letter-spacing: .5px; line-height: 1.1;
  }
  .contact .title {
    color: var(--pale); font-size: 13px; letter-spacing: .8px; margin-top: 2px;
  }
  .contact .rule { width: 54px; height: 2px; margin: 12px 0; }
  .contact .rule-teal { background: var(--lime); }
  .contact .rule-ocean { background: var(--ocean); margin: 12px 0 0; }
  .contact .details {
    color: var(--soft); font-size: 13px; letter-spacing: .6px; line-height: 1.35;
  }
  .contact .details .phone { font-size: 17px; color: var(--pale); }

  /* Front side: brand */
  .card-front .accent {
    position: absolute; top: 112px; height: 86px; display: flex; gap: 6px;
  }
  .card-front .accent-left { left: 0; }
  .card-front .accent-right { right: 0; flex-direction: row-reverse; }
  .card-front .accent .block {
    width: 40px; height: 100%;
    background: linear-gradient(180deg, var(--lime), var(--teal));
  }
  .card-front .accent .line { width: 4px; height: 100%; background: var(--ocean); }
  .brand {
    position: absolute; inset: 0;
    display: flex; align-items: center; justify-content: center; gap: 16px;
  }
  .brand .mark { width: 30px; height: 30px; background: var(--teal); }
  .brand .wordmark {
    color: var(--pale); font-weight: 600; font-size: 40px; letter-spacing: 1px; text-transform: uppercase;
  }
</style>
</head>
<body>
<main class="canvas">
  <section class="card card-back" aria-label="Card back with contact details">
    <div class="band-top"></div>
    <div class="contact">
      <p class="name">Marcus Hale</p>
      <p class="title">Managing Director</p>
      <div class="rule rule-teal"></div>
      <div class="details">
        <p class="phone">044-555 218 930</p>
        <p>info@verodex-trade.com</p>
        <p>www.verodex-trade.com</p>
      </div>
      <div class="rule rule-ocean"></div>
    </div>
    <div class="band-bottom"></div>
  </section>

  <section class="card card-front" aria-label="Card front with brand name">
    <div class="accent accent-left"><span class="block"></span><span class="line"></span></div>
    <div class="brand">
      <span class="mark"></span>
      <span class="wordmark">Verodex</span>
    </div>
    <div class="accent accent-right"><span class="block"></span><span class="line"></span></div>
  </section>
</main>
</body>
</html>
```